Design a Travel and Tourism website

We would like a freelancer to design a website that is essentially easy to use and navigate database providing local information for Travelers about destination countries.

We proposed website would discuss different rates, fees, visa requirement, resort locations, cheap flights, etc. This website should be elegant and modern. Our business name is rovanix.
Some reference websites are zemplorift.ca, brindlefoxhaven.com,
There should be a forum in the website where travell\ers discuss about their first hand tranvel experience to such destinations.

Tourism

```html
<!DOCTYPE html>
<html lang="en">
<head>
<meta charset="utf-8">
<title>Rovanix — Travel &amp; Tourism</title>
<link href="https://fonts.googleapis.com/css2?family=Montserrat:wght@400;600;700&family=Open+Sans:wght@400;600;700&family=Great+Vibes&display=swap" rel="stylesheet">
<style>
:root{
  --navy:#1c2b5e;
  --navy-deep:#162250;
  --blue:#1b8fd8;
  --blue-mid:#1679c2;
  --gold:#b89b5e;
  --gold-dark:#a4884d;
  --ink:#2b2b2b;
  --muted:#777;
  --line:#e2e2e2;
  --paper:#f1f1f1;
  --white:#fff;
}
*{box-sizing:border-box;margin:0;padding:0}
html,body{width:1200px;height:3243px;overflow:hidden}
body{font-family:"Open Sans",sans-serif;color:var(--ink);background:var(--white);position:relative}
.abs{position:absolute}

/* top bar + nav */
.topbar{height:22px;background:var(--navy);position:relative}
.topbar .social{position:absolute;left:143px;top:4px;display:flex;gap:4px}
.topbar .social span{width:14px;height:14px;border-radius:50%;background:#5f7fc0;display:block}
.topbar .util{position:absolute;right:143px;top:5px;display:flex;gap:18px;font:600 9px "Montserrat",sans-serif;color:#c9d3ee;letter-spacing:.5px}
.mainnav{height:43px;background:var(--blue);position:relative}
.mainnav ul{list-style:none;display:flex;position:absolute;top:0;height:43px}
.mainnav li{font:700 11.5px "Montserrat",sans-serif;color:var(--white);padding:0 20px;line-height:43px;letter-spacing:.3px}
.mainnav li.active{background:var(--gold)}
.mainnav .left{left:143px}
.mainnav .right{right:143px}
.logo-tab{position:absolute;left:515px;top:0;width:170px;height:92px;background:var(--white);border-radius:0 0 40px 40px;z-index:3;display:flex;align-items:center;justify-content:center;box-shadow:0 2px 6px rgba(0,0,0,.15)}
.brand{font:700 26px "Montserrat",sans-serif;color:var(--navy);display:flex;align-items:center;gap:6px}
.brand i{width:10px;height:10px;border-radius:50%;background:var(--blue);display:block}

/* hero */
.hero{height:346px;position:relative;background:linear-gradient(160deg,#8fb7c6 0%,#c4a98a 45%,#6e8a6a 75%,#3f5563 100%);overflow:hidden}
.hero-title{position:absolute;left:258px;top:157px;font:400 52px/58px "Great Vibes",cursive;color:var(--white);text-shadow:0 2px 6px rgba(0,0,0,.4)}
.offer{position:absolute;left:745px;top:97px;width:140px;height:140px;border-radius:50%;background:var(--navy);border:3px solid var(--gold);box-shadow:0 0 0 5px rgba(28,43,94,.5);text-align:center;color:var(--white);padding-top:26px}
.offer h3{font:700 17px/17px "Montserrat",sans-serif}
.offer p{font-size:10px;margin-top:4px}
.offer p b{color:var(--gold);font-size:14px}
.offer .mini{font:700 11px "Montserrat",sans-serif;color:#8fc4ee;margin-top:6px;border-top:1px solid var(--gold);display:inline-block;padding-top:4px}
.dots{position:absolute;left:588px;bottom:12px;display:flex;gap:5px}
.dots span{width:5px;height:5px;border-radius:50%;background:rgba(255,255,255,.7)}

/* search */
.search{height:209px;background:var(--navy);position:relative}
.tabs{position:absolute;top:35px;left:0;right:0;display:flex;justify-content:center;gap:4px}
.tabs span{font:700 10px "Montserrat",sans-serif;color:var(--white);background:var(--navy-deep);padding:7px 11px;border:1px solid #2e3f77}
.tabs span.on{background:var(--gold);border-color:var(--gold)}
.fields{position:absolute;top:67px;left:143px;display:flex;gap:4px}
.field label{display:block;font:700 8px "Montserrat",sans-serif;color:var(--white);margin-bottom:4px;white-space:nowrap}
.field .box{height:32px;background:var(--white);font-size:9.5px;color:#999;display:flex;align-items:center;padding:0 8px;gap:6px;justify-content:space-between}
.search .addcar{position:absolute;left:458px;top:152px;font:700 10px "Montserrat",sans-serif;color:var(--white);display:flex;align-items:center;gap:6px}
.addcar i{width:9px;height:9px;background:var(--white);display:block}
.btn{background:var(--blue);color:var(--white);font:700 11px "Montserrat",sans-serif;display:flex;align-items:center;justify-content:center}
.search .btn{position:absolute;left:552px;top:143px;width:95px;height:34px}

/* section headings */
.h2{font:700 27px "Montserrat",sans-serif;text-align:center;color:#333;letter-spacing:.5px}
.subtabs{text-align:center;font:700 9.5px "Montserrat",sans-serif;color:var(--gold);margin-top:12px;letter-spacing:.3px}
.subtabs .on{color:var(--blue)}
.subtabs em{font-style:normal;color:#bbb;margin:0 8px}

/* destinations */
.destinations{height:617px;position:relative}
.destinations .h2{padding-top:52px}
.tile{position:absolute;box-shadow:0 3px 8px rgba(0,0,0,.25)}
.tile .frame{position:absolute;inset:8px;border:1px solid rgba(255,255,255,.7)}
.tile .cap{position:absolute;left:20px;bottom:20px;font:600 15px "Open Sans",sans-serif;color:var(--white)}
.bangkok{background:linear-gradient(140deg,#1a62b5,#1d4f9a);color:var(--white);text-align:center;padding-top:60px}
.bangkok h4{font:600 25px "Open Sans",sans-serif}
.bangkok p{font-size:12px;line-height:15px;margin-top:6px}

/* hotels */
.hotels{height:456px;background:linear-gradient(180deg,#1e8ed6,#1677c0);position:relative;color:var(--white)}
.hotels .h2{color:var(--white);padding-top:56px}
.hotels .subtabs{color:var(--white)}
.hotels .subtabs em{color:rgba(255,255,255,.6)}
.hcard{position:absolute;top:153px;width:290px}
.hcard .img{height:188px;position:relative;box-shadow:0 3px 8px rgba(0,0,0,.3)}
.hcard .img .frame{position:absolute;inset:7px;border:1px solid rgba(255,255,255,.6)}
.hcard h5{font:600 13px "Open Sans",sans-serif;margin-top:9px}
.hcard p{font-size:10.5px;color:#b4dcf6}
.hcard .stars{color:#f4c542;font-size:10px;letter-spacing:1px}
.arrow{position:absolute;top:230px}

/* forum */
.forum{height:620px;background:var(--paper);position:relative}
.forum .h2{padding-top:56px}
.forum .tag{text-align:center;font:700 9.5px "Montserrat",sans-serif;color:var(--gold);margin-top:6px}
.table{position:absolute;left:143px;top:134px;width:914px;background:var(--white);border:1px solid var(--line)}
.thead{height:38px;background:var(--gold);color:var(--white);font:700 10px "Montserrat",sans-serif;display:flex;align-items:center;position:relative}
.row{height:66px;border-top:1px solid var(--line);position:relative}
.c-title{position:absolute;left:22px}
.c-date{position:absolute;left:546px}
.c-views{position:absolute;right:22px;text-align:right}
.thead span{top:13px}
.row .c-title{top:18px}
.row .c-title b{display:block;font:600 13px "Open Sans",sans-serif;color:var(--gold-dark)}
.row .c-title small{font-size:10px;color:#444}
.row .c-date{top:20px;font-size:10px;color:#444}
.row .c-views{top:20px;font-size:10px;color:#444;line-height:13px}
.row .c-views span{color:var(--gold-dark)}
.forum .btn{position:absolute;left:551px;top:545px;width:98px;height:32px}

/* newsletter */
.newsletter{height:173px;background:linear-gradient(90deg,#0f5fa8,#1a7cc6 50%,#1b6ab1);position:relative;color:var(--white);text-align:center}
.newsletter h3{font:700 19px "Montserrat",sans-serif;padding-top:40px}
.newsletter p{font:700 9.5px "Montserrat",sans-serif;margin-top:3px}
.nl-input{position:absolute;left:383px;top:93px;width:339px;height:37px;background:var(--white);color:#aaa;font-size:10px;display:flex;align-items:center;padding-left:14px;gap:8px;text-align:left}
.nl-input i{width:11px;height:8px;background:var(--gold);display:block}
.nl-submit{position:absolute;left:729px;top:93px;width:88px;height:37px;background:var(--gold);font:700 10.5px "Montserrat",sans-serif;line-height:37px}

/* popular links */
.popular{height:422px;position:relative}
.popular .h2{padding-top:54px}
.plink{position:absolute;width:289px;height:52px}
.plink svg{position:absolute;inset:0}
.plink span{position:absolute;left:46px;top:17px;font:600 13px "Montserrat",sans-serif;color:#333}

/* footer */
.footer{height:335px;position:relative;background:linear-gradient(180deg,#fff 0%,#fff 30%,#dfeef9 60%,#b8d8f0 100%);text-align:center;overflow:hidden}
.footer .brand{justify-content:center;padding-top:60px;font-size:24px}
.footer .social{display:flex;justify-content:center;gap:5px;margin-top:12px}
.footer .social span{width:24px;height:24px;border-radius:50%;background:#333;display:block}
.footer nav{margin-top:14px;font:700 10px "Montserrat",sans-serif;color:#333;display:flex;justify-content:center;gap:26px}
.footer .copy{font-size:9.5px;color:#555;margin-top:6px}
.skyline{position:absolute;left:0;right:0;bottom:0;height:150px;background:linear-gradient(180deg,rgba(44,70,140,.2),#2d4a8f 55%,#1e2f66)}
</style>
</head>
<body>

<header>
  <div class="topbar">
    <div class="social"><span></span><span></span><span></span></div>
    <div class="util"><span>ACCOUNT ▾</span><span>MY TRIPS</span><span>SUPPORT ▾</span></div>
  </div>
  <nav class="mainnav">
    <ul class="left"><li class="active">HOME</li><li>HOLIDAYS</li><li>FLIGHTS</li><li>HOTELS</li></ul>
    <div class="logo-tab"><span class="brand">Rovanix<i></i></span></div>
    <ul class="right"><li>CARS</li><li>DEALS</li><li>INSURANCE</li><li>FORUM</li></ul>
  </nav>
</header>

<section class="hero" role="img" aria-label="Photo of a family with surfboards on a sunny palm-lined beach">
  <h1 class="hero-title">Start Your Dream<br>Holidays Right Here</h1>
  <div class="offer">
    <h3>HAWAII<br>BEACHES</h3>
    <p>From <b>$500</b> per person</p>
    <div class="mini">Rovanix</div>
  </div>
  <div class="dots"><span></span><span></span><span></span></div>
</section>

<section class="search">
  <div class="tabs"><span class="on">FLIGHT &amp; HOTEL</span><span>HOLIDAYS</span><span>FLIGHTS</span><span>HOTELS</span><span>CARS</span><span>INSURANCE</span><span>EXTRAS</span></div>
  <div class="fields">
    <div class="field" style="width:228px"><label>FLYING FROM</label><div class="box"><span>⌖ City or Airport</span></div></div>
    <div class="field" style="width:228px"><label>FLYING TO</label><div class="box"><span>⌖ City or Airport</span></div></div>
    <div class="field" style="width:120px"><label>DEPARTING</label><div class="box"><span>▦ dd/mm/yyyy</span></div></div>
    <div class="field" style="width:122px"><label>RETURNING</label><div class="box"><span>▦ dd/mm/yyyy</span></div></div>
    <div class="field" style="width:52px"><label>ROOMS</label><div class="box"><span style="color:#333">1</span><span>▾</span></div></div>
    <div class="field" style="width:68px"><label>ADULTS (18+)</label><div class="box"><span style="color:#333">2</span><span>▾</span></div></div>
    <div class="field" style="width:80px"><label>CHILDREN (0-17)</label><div class="box"><span style="color:#333">0</span><span>▾</span></div></div>
  </div>
  <div class="addcar"><i></i>ADD A CAR</div>
  <div class="btn">SEARCH</div>
</section>

<section class="destinations">
  <h2 class="h2">DESTINATIONS</h2>
  <div class="subtabs"><span class="on">TOP DESTINATIONS</span><em>|</em>FEATURED DESTINATIONS<em>|</em>POPULAR DESTINATIONS</div>
  <div class="tile" style="left:143px;top:150px;width:218px;height:406px;background:linear-gradient(160deg,#c9a58a,#8a5a48 50%,#3e4a66)" role="img" aria-label="Photo of New York skyscrapers"><div class="frame"></div><div class="cap">New York</div></div>
  <div class="tile bangkok" style="left:376px;top:150px;width:448px;height:194px"><div class="frame"></div><h4>Bangkok</h4><p>Lorem ipsum dolor sit amet, consectetur adipiscing elit,<br>do eiusmod tempor incididunt ut labore.</p></div>
  <div class="tile" style="left:376px;top:364px;width:448px;height:192px;background:linear-gradient(180deg,#3b5a9a,#c8705a 55%,#e2a060)" role="img" aria-label="Photo of the Las Vegas welcome sign at sunset"><div class="frame"></div><div class="cap">Las Vegas</div></div>
  <div class="tile" style="left:839px;top:150px;width:218px;height:406px;background:linear-gradient(180deg,#6d93c8,#8aa2a0 45%,#5d6a3a)" role="img" aria-label="Photo of a hula dancer in Hawaii"><div class="frame"></div><div class="cap">Hawaii</div></div>
</section>

<section class="hotels">
  <h2 class="h2">HOTELS</h2>
  <div class="subtabs"><span>LUXURY HOTELS</span><em>|</em>CHEAP HOTELS<em>|</em>POPULAR HOTELS</div>
  <svg class="arrow" style="left:84px" width="18" height="30" viewBox="0 0 18 30"><path d="M15 2 3 15l12 13" fill="none" stroke="#fff" stroke-width="3"/></svg>
  <svg class="arrow" style="left:1096px" width="18" height="30" viewBox="0 0 18 30"><path d="M3 2l12 13L3 28" fill="none" stroke="#fff" stroke-width="3"/></svg>
  <div class="hcard" style="left:143px"><div class="img" style="background:linear-gradient(160deg,#8bb6e0,#5a6f8e 55%,#8a5a40)" role="img" aria-label="Photo of a glass tower in London"><div class="frame"></div></div><h5>London, UK</h5><p>Fantacy Serviced Apartments</p><div class="stars">★★★★★</div></div>
  <div class="hcard" style="left:454px"><div class="img" style="background:linear-gradient(180deg,#7fb0e0,#c9c3b5 45%,#8d8778)" role="img" aria-label="Photo of a classic building in Paris"><div class="frame"></div></div><h5>Paris, France</h5><p>Fantacy Serviced Apartments</p><div class="stars">★★★★★</div></div>
  <div class="hcard" style="left:768px"><div class="img" style="background:linear-gradient(180deg,#2b4f8c,#5a7bb0 50%,#c89a60)" role="img" aria-label="Photo of modern towers in Berlin at dusk"><div class="frame"></div></div><h5>Berlin, Germany</h5><p>Fantacy Serviced Apartments</p><div class="stars">★★★★★</div></div>
</section>

<section class="forum">
  <h2 class="h2">LATEST TRAVEL FORUM</h2>
  <div class="tag">PLEASE SHARE YOUR EXPERIENCE HERE</div>
  <div class="table">
    <div class="thead"><span class="c-title">TITLE</span><span class="c-date">POSTED ON</span><span class="c-views">VIEWS / REPLIES</span></div>
    <div class="row"><div class="c-title"><b>Why Hawaii is a hub for entertainment?</b><small>By : Oskar Lindqvist</small></div><div class="c-date">15 Jan 2017, 07:45 AM</div><div class="c-views">View : <span>1450</span><br>Replies : <span>45</span></div></div>
    <div class="row"><div class="c-title"><b>Whis the hottest place in January?</b><small>By : Pavel Drenko</small></div><div class="c-date">15 Jan 2017, 06:45 AM</div><div class="c-views">View : <span>1950</span><br>Replies : <span>75</span></div></div>
    <div class="row"><div class="c-title"><b>Must visit destinations in the world which make you feel better...</b><small>By : Pavel Drenko</small></div><div class="c-date">15 Jan 2017, 06:45 AM</div><div class="c-views">View : <span>1950</span><br>Replies : <span>75</span></div></div>
    <div class="row"><div class="c-title"><b>Why Hawaii is a hub for entertainment?</b><small>By : Oskar Lindqvist</small></div><div class="c-date">15 Jan 2017, 07:45 AM</div><div class="c-views">View : <span>1450</span><br>Replies : <span>45</span></div></div>
    <div class="row"><div class="c-title"><b>Whis the hottest place in January?</b><small>By : Pavel Drenko</small></div><div class="c-date">15 Jan 2017, 06:45 AM</div><div class="c-views">View : <span>1950</span><br>Replies : <span>75</span></div></div>
  </div>
  <div class="btn">VIEW ALL</div>
</section>

<section class="newsletter">
  <h3>SIGN UP TO OUR NEWSLETTER</h3>
  <p>GET UPDATED FOR SPECIAL OFFERS</p>
  <div class="nl-input"><i></i>Enter your email address</div>
  <div class="nl-submit">SUBMIT</div>
</section>

<section class="popular">
  <h2 class="h2">POPULAR LINKS YOU MAY INTERESTED</h2>
  <svg width="0" height="0" style="position:absolute"><defs>
    <symbol id="plinkbox" viewBox="0 0 289 52"><path d="M.5 .5H274L288.5 26 274 51.5H.5Z" fill="#fff" stroke="#ddd"/><path d="M18 26l5 5 9-11" fill="none" stroke="#b89b5e" stroke-width="2.5"/></symbol>
  </defs></svg>
  <div class="plink" style="left:143px;top:121px"><svg viewBox="0 0 289 52"><use href="#plinkbox"/></svg><span>New York Holidays</span></div>
  <div class="plink" style="left:454px;top:121px"><svg viewBox="0 0 289 52"><use href="#plinkbox"/></svg><span>Amsterdam Hotels</span></div>
  <div class="plink" style="left:768px;top:121px"><svg viewBox="0 0 289 52"><use href="#plinkbox"/></svg><span>Dubai Holidays</span></div>
  <div class="plink" style="left:143px;top:180px"><svg viewBox="0 0 289 52"><use href="#plinkbox"/></svg><span>UK Car Hire</span></div>
  <div class="plink" style="left:454px;top:180px"><svg viewBox="0 0 289 52"><use href="#plinkbox"/></svg><span>Oralando Flights</span></div>
  <div class="plink" style="left:768px;top:180px"><svg viewBox="0 0 289 52"><use href="#plinkbox"/></svg><span>Bangkok Flights</span></div>
  <div class="plink" style="left:143px;top:239px"><svg viewBox="0 0 289 52"><use href="#plinkbox"/></svg><span>Sydney Flights</span></div>
  <div class="plink" style="left:454px;top:239px"><svg viewBox="0 0 289 52"><use href="#plinkbox"/></svg><span>Hawaii Hotels</span></div>
  <div class="plink" style="left:768px;top:239px"><svg viewBox="0 0 289 52"><use href="#plinkbox"/></svg><span>Paris Car Hire</span></div>
  <div class="plink" style="left:143px;top:298px"><svg viewBox="0 0 289 52"><use href="#plinkbox"/></svg><span>New York Holidays</span></div>
  <div class="plink" style="left:454px;top:298px"><svg viewBox="0 0 289 52"><use href="#plinkbox"/></svg><span>Amsterdam Hotels</span></div>
  <div class="plink" style="left:768px;top:298px"><svg viewBox="0 0 289 52"><use href="#plinkbox"/></svg><span>Dubai Holidays</span></div>
  <div class="plink" style="left:143px;top:357px"><svg viewBox="0 0 289 52"><use href="#plinkbox"/></svg><span>UK Car Hire</span></div>
  <div class="plink" style="left:454px;top:357px"><svg viewBox="0 0 289 52"><use href="#plinkbox"/></svg><span>Oralando Flights</span></div>
  <div class="plink" style="left:768px;top:357px"><svg viewBox="0 0 289 52"><use href="#plinkbox"/></svg><span>Bangkok Flights</span></div>
</section>

<footer class="footer">
  <div class="skyline" role="img" aria-label="City skyline silhouette over the sea"></div>
  <div style="position:relative">
    <div class="brand">Rovanix<i></i></div>
    <div class="social"><span></span><span></span><span></span></div>
    <nav><span>HOME</span><span>ABOUT US</span><span>CUSTOMER SUPPORT</span><span>PRIVACY</span><span>TERMS OF USE</span></nav>
    <div class="copy">© 2016 ROVANIX. ALL RIGHTS RESERVED.</div>
  </div>
</footer>

</body>
</html>
```